Modern Verdell Tree Care Website

I need a website for a full service Tree Care company. The company provides tree pruning, tree removal, tree preservation, emergency services, stump grinding, and emergency tree services.

Target Market(s)

Customers that need tree services

Industry/Entity Type

Landscaping, Tree Services

Coding

Coded - Design and coding required

Number of Pages Required

5+ page

Font styles to use
Sans Serif

Requirements
Must have
• Good clean design that showcases the services the company provides.
Nice to have
• Services page; contact form, blog, home page, about page

```html
<!DOCTYPE html>
<html lang="en">
<head>
<meta charset="utf-8">
<title>Verdell Tree Care</title>
<link href="https://fonts.googleapis.com/css2?family=Fira+Sans:wght@500;600;700&family=Open+Sans:wght@400;600;700&display=swap" rel="stylesheet">
<style>
:root{
  --green:#7dc142;
  --green-dark:#5e9e2c;
  --navy:#0f1c47;
  --navy-deep:#0d1733;
  --orange:#f39c32;
  --text:#333a44;
  --muted:#8a909a;
  --cream:#f7f5ef;
  --steps-bg:#e9edf5;
  --white:#ffffff;
}
*{margin:0;padding:0;box-sizing:border-box}
html,body{width:1200px;height:4189px;overflow:hidden}
body{position:relative;font-family:"Open Sans",sans-serif;color:var(--text);background:var(--white)}
.abs{position:absolute}
.heading{font-family:"Fira Sans",sans-serif;font-weight:600;color:var(--navy)}
.label{font-size:13px;color:var(--green-dark);text-align:center;width:100%;letter-spacing:.2px}
.label span{border-bottom:1px solid var(--green);padding-bottom:3px}
.btn-green{background:var(--green);color:var(--white);font-weight:600;font-size:14px;display:flex;align-items:center;justify-content:center;gap:14px}

/* header */
.topbar{left:385px;top:0;width:815px;height:33px;background:var(--navy);color:var(--white);font-size:11px;font-weight:600}
.topbar .item{position:absolute;top:0;height:33px;display:flex;align-items:center;gap:8px}
.topbar .appt{left:208px;width:228px;background:var(--green);justify-content:center;font-weight:400}
.brand{left:98px;top:20px;display:flex;align-items:center;gap:10px}
.brand .mark{width:52px;height:52px;background:var(--green)}
.brand .name{font-family:"Fira Sans",sans-serif;font-weight:600;font-size:24px;color:var(--navy);line-height:1}
.nav{top:61px;left:395px;font-size:12px;font-weight:600;color:#333}
.nav span{position:absolute;white-space:nowrap}
.cta-outline{left:930px;top:53px;width:118px;height:30px;border:1.5px solid var(--orange);border-radius:4px;color:var(--orange);font-size:11px;display:flex;align-items:center;justify-content:center}

/* hero */
.hero{left:0;top:94px;width:1200px;height:680px;background:linear-gradient(90deg,#fafbf8 0%,#eef1ea 30%,rgba(150,170,120,.6) 55%,#6b7d4c 75%,#4f5f36 100%)}
.hero-fade{left:0;top:94px;width:700px;height:680px;background:linear-gradient(90deg,rgba(255,255,255,.95),rgba(255,255,255,.5) 70%,rgba(255,255,255,0))}
.eyebrow{left:124px;top:264px;font-family:"Fira Sans",sans-serif;font-weight:600;font-size:21px;letter-spacing:5px;color:#111}
.hero-title{left:118px;top:308px;font-family:"Fira Sans",sans-serif;font-weight:700;font-size:68px;color:var(--navy);line-height:1}
.hero-rule{left:124px;top:402px;width:496px;height:2px;background:var(--green)}
.hero-copy{left:124px;top:425px;width:500px;font-size:15.5px;line-height:28px;color:#222}
.pill{top:512px;height:40px;border-radius:20px;font-size:14px;font-weight:700;color:var(--white);display:flex;align-items:center;justify-content:center}

/* who we are */
.who-img{left:120px;top:972px;width:495px;height:340px;border-radius:12px;background:linear-gradient(160deg,#c7d0d8,#8f9a8c 50%,#5b6650)}
.who-card{left:561px;top:998px;width:517px;height:306px;background:var(--cream);border-radius:8px}
.who-card h3{position:absolute;left:37px;top:50px;font-family:"Fira Sans",sans-serif;font-weight:500;font-size:20px;color:#222}
.who-card p{position:absolute;left:37px;width:450px;font-size:12.5px;line-height:19.5px;color:var(--muted)}

/* services */
.services{left:0;top:1416px;width:1200px;height:556px;background:radial-gradient(ellipse at 50% 40%,#4a4a42,#2a2b27 70%,#1f201d)}
.svc{top:1605px;width:304px;height:228px;overflow:hidden}
.svc .photo{position:absolute;inset:0}
.svc .shade{position:absolute;left:0;right:0;bottom:0;height:120px;background:linear-gradient(0deg,rgba(0,0,0,.85),rgba(0,0,0,0))}
.svc h4{position:absolute;left:84px;top:160px;font-family:"Fira Sans",sans-serif;font-weight:600;font-size:16px;color:var(--white)}
.svc p{position:absolute;left:84px;top:186px;font-size:13px;color:var(--white)}
.svc svg.ic{position:absolute;left:34px;top:163px}

/* steps */
.steps{left:0;top:1972px;width:1200px;height:500px;background:var(--steps-bg)}
.step{width:260px;text-align:center}
.step h5{font-family:"Fira Sans",sans-serif;font-weight:600;font-size:18px;color:var(--navy)}
.step p{margin-top:6px;font-size:13px;line-height:21px;color:var(--muted)}

/* sustainable */
.sust{left:0;top:2472px;width:1200px;height:574px;background:linear-gradient(90deg,#b8c59a 0%,#6d8a43 35%,#2a3a1c 60%,#17200f 100%)}
.sust-item{left:630px;display:flex;gap:18px;align-items:center;color:var(--white)}
.sust-item .circ{width:60px;height:60px;border-radius:50%;background:var(--white);display:flex;align-items:center;justify-content:center;flex:none}
.sust-item h6{font-family:"Fira Sans",sans-serif;font-weight:600;font-size:18px}
.sust-item p{font-size:12.5px;margin-top:2px}

/* testimonials */
.avatar{border-radius:50%;background:linear-gradient(150deg,#c9ccd2,#8c8f98)}
.quote-text{left:290px;top:3382px;width:620px;text-align:center;font-size:14.5px;line-height:22px;color:#222}

/* footer */
.foot-nav{top:3948px;left:0;width:1200px;font-size:14.5px;color:var(--white)}
.foot-nav span{position:absolute}
.contact{top:4046px;display:flex;align-items:center;gap:12px;color:var(--white);font-size:12px;line-height:19px}
.contact .ring{width:54px;height:54px;border-radius:50%;border:1.5px solid rgba(255,255,255,.7);display:flex;align-items:center;justify-content:center}
.contact b{font-weight:400;font-size:14px}
.bottom{left:0;top:4130px;width:1200px;height:59px;background:var(--green);color:var(--white);font-size:12px}
.social{top:4146px;width:25px;height:25px;border:1.5px solid var(--white);border-radius:3px}
</style>
</head>
<body>

<!-- header -->
<div class="abs topbar">
  <div class="item" style="left:58px">
    <svg width="15" height="15" viewBox="0 0 24 24" fill="none" stroke="#fff" stroke-width="2"><path d="M5 3h4l2 5-2.5 1.5a11 11 0 0 0 6 6L16 13l5 2v4a2 2 0 0 1-2 2A16 16 0 0 1 3 5a2 2 0 0 1 2-2z"/></svg>
    555 - 014 - 2290
  </div>
  <div class="item appt">
    <svg width="14" height="14" viewBox="0 0 24 24" fill="none" stroke="#fff" stroke-width="2"><rect x="3" y="5" width="18" height="16" rx="2"/><path d="M3 10h18M8 3v4M16 3v4"/></svg>
    REQUEST AN APPOINTMENT
  </div>
  <div class="item" style="left:472px;font-weight:400">
    <svg width="12" height="14" viewBox="0 0 24 28" fill="none" stroke="#fff" stroke-width="2.4"><path d="M12 26s9-9 9-15a9 9 0 0 0-18 0c0 6 9 15 9 15z"/><circle cx="12" cy="11" r="3"/></svg>
    88 Cedar Hollow Road
  </div>
</div>
<div class="abs brand">
  <div class="mark"></div>
  <div class="name">Verdell Tree Care</div>
</div>
<div class="abs nav">
  <span style="left:0">Home</span>
  <span style="left:75px">About Us</span>
  <span style="left:150px">Solutions</span>
  <span style="left:225px">Projects</span>
  <span style="left:331px">Our Team</span>
</div>
<div class="abs cta-outline">CONTACT US</div>

<!-- hero -->
<div class="abs hero" role="img" aria-label="Arborist in safety gear cutting a large tree trunk"></div>
<div class="abs hero-fade"></div>
<svg class="abs" style="left:0;top:690px" width="1200" height="90" viewBox="0 0 1200 90">
  <path d="M0 40 C250 5 520 20 760 50 C950 72 1100 60 1200 10 L1200 90 L0 90Z" fill="#fff"/>
  <path d="M0 35 C250 0 520 14 760 44 C950 66 1100 52 1200 2 L1200 20 C1100 72 950 82 760 62 C520 32 250 18 0 40Z" fill="var(--green)"/>
</svg>
<div class="abs eyebrow">Experts in</div>
<div class="abs hero-title">Tree Care</div>
<div class="abs hero-rule"></div>
<p class="abs hero-copy">Lorem ipsum dolor sit amet, consectetur adipiscing elit, sed do eiusmod tempor incididunt ut labore</p>
<div class="abs pill" style="left:125px;width:145px;background:var(--green)">LEARN MORE</div>
<div class="abs pill" style="left:281px;width:180px;background:#000">REQUEST QUOTE</div>

<!-- who we are -->
<div class="abs label" style="top:844px"><span>WHO WE ARE</span></div>
<h2 class="abs heading" style="top:882px;width:1200px;text-align:center;font-size:40px">Your Trees, Our Expertise</h2>
<div class="abs who-img" role="img" aria-label="Arborist climbing among bare tree branches with a chainsaw"></div>
<div class="abs who-card">
  <h3>Your Partner in Tree Presevation</h3>
  <p style="top:88px">Lorem ipsum dolor sit amet, consectetur adipiscing elit, sed do eiusmod temp or incididunt ut labore et dolore magna aliqua. Ut enim ad minim veniam, quis laboris nisi ut aliquip ex ea commodo consequat.</p>
  <p style="top:156px">Lorem ipsum dolor sit amet, consectetur adipiscing elit, sed do eiusmod temp or incididunt ut labore et dolore magna aliqua.</p>
</div>
<div class="abs btn-green" style="left:602px;top:1228px;width:136px;height:38px">Contact us
  <svg width="16" height="12" viewBox="0 0 16 12" fill="none" stroke="#fff" stroke-width="1.6"><path d="M1 6h13M9 1l5 5-5 5"/></svg>
</div>

<!-- services -->
<div class="abs services" role="img" aria-label="Dark forest canopy background"></div>
<div class="abs label" style="top:1472px;color:#fff"><span style="border-color:#fff">OUR SERVICES</span></div>
<h2 class="abs heading" style="top:1510px;width:1200px;text-align:center;font-size:40px;color:#fff">Services We Provide</h2>

<div class="abs svc" style="left:119px">
  <div class="photo" role="img" aria-label="Tree pruning scene with green overlay" style="background:linear-gradient(135deg,#8ccc52,#6fb536 60%,#5fa42b)"></div>
  <div class="abs" style="left:0;top:72px;width:304px;text-align:center;color:#fff">
    <div style="font-family:'Fira Sans',sans-serif;font-weight:600;font-size:16px">Tree Pruning</div>
    <div style="font-size:13px;line-height:21px;margin:4px auto 0;width:220px">Lorem ipsum dolor sit amet, con sectetur adipiscing elit, sed do eiusmod tempor</div>
    <svg style="margin-top:10px" width="26" height="14" viewBox="0 0 26 14" fill="none" stroke="#fff" stroke-width="1.6"><path d="M1 7h23M18 1l6 6-6 6"/></svg>
  </div>
</div>
<div class="abs svc" style="left:447px">
  <div class="photo" role="img" aria-label="Hands holding an uprooted tree root ball" style="background:linear-gradient(160deg,#8a7a55,#5c6b3a 50%,#3b4a28)"></div>
  <div class="shade"></div>
  <svg class="ic" width="30" height="30" viewBox="0 0 30 30" fill="none" stroke="var(--green)" stroke-width="1.6"><path d="M4 26h22M8 22c4-2 8-2 12 0M15 20V8M15 8c-4 0-6-3-6-6 4 0 6 3 6 6zM15 12c3 0 6-2 6-5-3 0-6 2-6 5z"/></svg>
  <h4>Tree Removal</h4>
  <p>Inventore veritasis uas vite</p>
</div>
<div class="abs svc" style="left:776px">
  <div class="photo" role="img" aria-label="Two workers tending saplings in a tree nursery row" style="background:linear-gradient(160deg,#6f8f55,#4c6a38 50%,#2f3f24)"></div>
  <div class="shade"></div>
  <svg class="ic" width="30" height="30" viewBox="0 0 30 30" fill="none" stroke="var(--green)" stroke-width="1.6"><path d="M15 3l3.5 7 7.5 1-5.5 5.5 1.3 7.5L15 20.5 8.2 24l1.3-7.5L4 11l7.5-1z"/></svg>
  <h4>Stump Grinding</h4>
  <p>Inventore veritasis uas vite</p>
</div>
<div class="abs btn-green" style="left:548px;top:1883px;width:135px;height:39px">Contact us
  <svg width="16" height="12" viewBox="0 0 16 12" fill="none" stroke="#fff" stroke-width="1.6"><path d="M1 6h13M9 1l5 5-5 5"/></svg>
</div>

<!-- steps -->
<div class="abs steps"></div>
<div class="abs label" style="top:2045px"><span>STEPS TO TAKE</span></div>
<h2 class="abs heading" style="top:2080px;width:1200px;text-align:center;font-size:40px">Steps To Take</h2>
<svg class="abs" style="left:0;top:2170px" width="1200" height="140" viewBox="0 0 1200 140">
  <line x1="340" y1="67" x2="538" y2="67" stroke="#4a8fb5" stroke-width="1.5"/>
  <line x1="656" y1="67" x2="852" y2="67" stroke="#4a8fb5" stroke-width="1.5"/>
  <g id="stepmarks" fill="none">
    <circle cx="281" cy="67" r="58" stroke="#4a8fb5" stroke-width="1.5" fill="#fff"/>
    <circle cx="281" cy="67" r="47" fill="var(--navy)"/>
    <circle cx="597" cy="67" r="58" stroke="#4a8fb5" stroke-width="1.5" fill="#fff"/>
    <circle cx="597" cy="67" r="47" fill="var(--navy)"/>
    <circle cx="911" cy="67" r="58" stroke="#4a8fb5" stroke-width="1.5" fill="#fff"/>
    <circle cx="911" cy="67" r="47" fill="var(--navy)"/>
  </g>
  <g stroke="#fff" stroke-width="1.8" fill="none">
    <path d="M263 84h36M268 79c5-3 13-3 18 0M281 77V58M281 58c-5 0-8-4-8-8 5 0 8 4 8 8zM281 64c4 0 8-3 8-7-4 0-8 3-8 7z"/>
    <path d="M579 84h36M584 79c5-3 13-3 18 0M597 77V58M597 58c-5 0-8-4-8-8 5 0 8 4 8 8zM597 64c4 0 8-3 8-7-4 0-8 3-8 7z"/>
    <path d="M893 84h36M898 79c5-3 13-3 18 0M911 77V58M911 58c-5 0-8-4-8-8 5 0 8 4 8 8zM911 64c4 0 8-3 8-7-4 0-8 3-8 7z"/>
  </g>
  <g font-family="Open Sans, sans-serif" font-size="11" font-weight="700" fill="#fff" text-anchor="middle">
    <circle cx="336" cy="67" r="13" fill="var(--green)"/><text x="336" y="71">01</text>
    <circle cx="652" cy="67" r="13" fill="var(--green)"/><text x="652" y="71">02</text>
    <circle cx="966" cy="67" r="13" fill="var(--green)"/><text x="966" y="71">03</text>
  </g>
</svg>
<div class="abs step" style="left:151px;top:2313px"><h5>Contact Us to Start</h5><p>Lorem ipsum dolor sit amet, consectetur adipiscing elit, sed do eiusmo</p></div>
<div class="abs step" style="left:467px;top:2313px"><h5>Get assigned an expert</h5><p>Lorem ipsum dolor sit amet, consectetur adipiscing elit, sed do eiusmo</p></div>
<div class="abs step" style="left:781px;top:2313px"><h5>Start the Sessions</h5><p>Lorem ipsum dolor sit amet, consectetur adipiscing elit, sed do eiusmo</p></div>

<!-- sustainable -->
<div class="abs sust" role="img" aria-label="Two smiling engineers in hard hats and safety vests holding plans in a green field"></div>
<div class="abs" style="left:634px;top:2564px;font-size:12px;color:var(--green)"><span style="border-bottom:1px solid var(--green);padding-bottom:3px">WHO WE ARE</span></div>
<h2 class="abs heading" style="left:634px;top:2597px;font-size:39px;line-height:47px;color:#fff">We Offer Sustainable<br>Tree Solutions</h2>
<div class="abs sust-item" style="top:2718px">
  <div class="circ"><svg width="30" height="30" viewBox="0 0 30 30" fill="none" stroke="var(--green)" stroke-width="1.6"><path d="M5 25h20M9 21c4-2 8-2 12 0M15 19V9M15 9c-4 0-6-3-6-6 4 0 6 3 6 6zM15 13c3 0 6-2 6-5-3 0-6 2-6 5z"/></svg></div>
  <div><h6>On-Time Appointments</h6><p>Inventore veritasis uasvitae dicta suntetur sipid</p></div>
</div>
<div class="abs sust-item" style="top:2798px">
  <div class="circ"><svg width="30" height="30" viewBox="0 0 30 30" fill="none" stroke="var(--green)" stroke-width="1.6"><path d="M6 18v-3a9 9 0 0 1 18 0v3"/><rect x="5" y="17" width="5" height="7" rx="1.5"/><rect x="20" y="17" width="5" height="7" rx="1.5"/></svg></div>
  <div><h6>Experienced Professionals</h6><p>Inventore veritasis uasvitae dicta suntetur sipid</p></div>
</div>
<div class="abs sust-item" style="top:2881px">
  <div class="circ"><svg width="30" height="30" viewBox="0 0 30 30" fill="none" stroke="var(--green)" stroke-width="1.6"><path d="M15 4l3.3 6.6 7.2 1-5.2 5.1 1.2 7.2L15 20.5l-6.5 3.4 1.2-7.2-5.2-5.1 7.2-1z"/></svg></div>
  <div><h6>Proven Track Record</h6><p>Inventore veritasis uasvitae dicta suntetur sipid</p></div>
</div>

<!-- testimonials -->
<div class="abs" style="left:0;top:3193px;width:1200px;text-align:center;font-size:17px;color:var(--green)">TESTIMONIALS</div>
<h2 class="abs heading" style="top:3220px;width:1200px;text-align:center;font-size:33px">What Our Clients are Saying</h2>
<div class="abs avatar" role="img" aria-label="Client portrait" style="left:91px;top:3358px;width:100px;height:100px"></div>
<div class="abs avatar" role="img" aria-label="Client portrait" style="left:243px;top:3303px;width:58px;height:58px"></div>
<div class="abs avatar" role="img" aria-label="Client portrait" style="left:263px;top:3419px;width:40px;height:40px"></div>
<div class="abs avatar" role="img" aria-label="Client portrait" style="left:172px;top:3494px;width:82px;height:82px"></div>
<div class="abs avatar" role="img" aria-label="Client portrait" style="left:895px;top:3311px;width:48px;height:48px"></div>
<div class="abs avatar" role="img" aria-label="Client portrait" style="left:1003px;top:3346px;width:104px;height:104px"></div>
<div class="abs avatar" role="img" aria-label="Client portrait" style="left:896px;top:3431px;width:56px;height:56px"></div>
<div class="abs avatar" role="img" aria-label="Client portrait" style="left:996px;top:3500px;width:80px;height:80px"></div>
<svg class="abs" style="left:567px;top:3303px" width="60" height="60" viewBox="0 0 60 60">
  <circle cx="30" cy="30" r="30" fill="var(--green)"/>
  <path d="M19 38l4-10h-4V20h9v8l-4 10zM32 38l4-10h-4V20h9v8l-4 10z" fill="#fff"/>
</svg>
<p class="abs quote-text">Lorem ipsum dolor sit amet, consectetur adipiscing elit, sed do eiusmod tempor incidi dunt ut labore et dolore magna aliqua .dipiscing elit, sed do eiusmod tempor incidi dunt ut labore et dolore magna aliqua .dipiscing elit, sed do eiusmod tempor incididunt</p>
<div class="abs" style="left:0;top:3483px;width:1200px;text-align:center;font-size:13px;color:var(--orange)">Marcus Halden</div>
<div class="abs" style="left:0;top:3505px;width:1200px;text-align:center;font-size:10px;color:#222">Client</div>
<svg class="abs" style="left:546px;top:3541px" width="100" height="44" viewBox="0 0 100 44">
  <circle cx="22" cy="22" r="21" fill="var(--navy-deep)"/>
  <path d="M30 22H14M20 16l-6 6 6 6" stroke="#fff" stroke-width="1.8" fill="none"/>
  <circle cx="77" cy="22" r="21" fill="var(--green)"/>
  <path d="M69 22h16M79 16l6 6-6 6" stroke="#fff" stroke-width="1.8" fill="none"/>
</svg>

<!-- footer -->
<svg class="abs" style="left:0;top:3686px" width="1200" height="100" viewBox="0 0 1200 100">
  <path d="M0 70 C200 20 430 10 650 45 C860 78 1050 50 1200 0 L1200 100 L0 100Z" fill="var(--green)"/>
  <path d="M0 90 C200 40 430 30 650 65 C860 98 1050 70 1200 25 L1200 100 L0 100Z" fill="var(--navy-deep)"/>
</svg>
<div class="abs" style="left:0;top:3780px;width:1200px;height:350px;background:var(--navy-deep)"></div>
<div class="abs" style="left:0;top:3852px;width:1200px;display:flex;justify-content:center;align-items:center;gap:16px">
  <div style="width:60px;height:60px;background:#fff"></div>
  <div style="font-family:'Fira Sans',sans-serif;font-weight:600;font-size:32px;color:#fff">Verdell Tree Care</div>
</div>
<div class="abs foot-nav">
  <span style="left:296px">HOME</span>
  <span style="left:390px">SERVICES</span>
  <span style="left:496px">ABOUT US</span>
  <span style="left:615px">TESTIMONIALS</span>
  <span style="left:765px">BLOG</span>
</div>
<div class="abs" style="left:141px;top:4000px;width:919px;height:1px;background:rgba(255,255,255,.35)"></div>
<div class="abs" style="left:398px;top:4035px;width:1px;height:78px;background:rgba(255,255,255,.4)"></div>
<div class="abs" style="left:718px;top:4035px;width:1px;height:78px;background:rgba(255,255,255,.4)"></div>
<div class="abs contact" style="left:142px">
  <div class="ring"><svg width="28" height="28" viewBox="0 0 28 28" fill="none" stroke="#fff" stroke-width="1.4"><circle cx="14" cy="14" r="11"/><path d="M3 14h22M14 3c4 4 4 18 0 22M14 3c-4 4-4 18 0 22"/></svg></div>
  <div>42 Elmstone Way,<br>Brookfield, OR 97001</div>
</div>
<div class="abs contact" style="left:474px">
  <div class="ring"><svg width="24" height="28" viewBox="0 0 24 28" fill="none" stroke="#fff" stroke-width="1.4"><rect x="6" y="3" width="12" height="22" rx="2"/><path d="M10 21h4"/></svg></div>
  <div><b>PHONE</b><br>(555) 210 4478</div>
</div>
<div class="abs contact" style="left:796px">
  <div class="ring"><svg width="28" height="26" viewBox="0 0 28 26" fill="none" stroke="#fff" stroke-width="1.4"><rect x="3" y="6" width="22" height="16" rx="1.5"/><path d="M3 7l11 8 11-8"/></svg></div>
  <div><b>EMAIL</b><br>hello@verdelltree.com</div>
</div>
<div class="abs bottom"><span style="position:absolute;left:147px;top:22px">Verdell Tree Care</span></div>
<div class="abs social" style="left:933px"></div>
<div class="abs social" style="left:966px"></div>
<div class="abs social" style="left:999px"></div>
<div class="abs social" style="left:1032px"></div>

</body>
</html>
```